Fernhale Business Card Design

We are looking for a fresh business card design for our new logo. We would like a business card that is unique but friendly. We are in the window coverings business offering blinds, shutters and shades for homes.

Target Market(s)

Targeting the end-consumer

Industry/Entity Type

Business

Requirements
Must have
• Must have a dedicates space for a photo of our sales person. Must contain our new logo (attached).

```html
<!DOCTYPE html>
<html lang="en">
<head>
<meta charset="utf-8">
<title>Fernhale Business Card</title>
<link rel="stylesheet" href="https://fonts.googleapis.com/css2?family=Alegreya+Sans:wght@500&family=Roboto:wght@400&family=Roboto+Condensed:wght@400;700&display=swap">
<style>
  :root {
    --backdrop: #2b2b2c;
    --card-front: #f2f2f2;
    --card-back-top: #6d6c71;
    --card-back-bottom: #8b8a8f;
    --brand-grey: #78787b;
    --text-grey: #555558;
    --leaf-green: #7cc142;
    --photo-fill: #d6d7d9;
    --photo-frame: #111;
    --white: #ffffff;
  }
  html, body {
    margin: 0;
    width: 1200px;
    height: 960px;
    overflow: hidden;
    background: var(--backdrop);
  }
  .canvas {
    position: relative;
    width: 1200px;
    height: 960px;
  }
  .card {
    position: absolute;
    width: 600px;
    height: 343px;
    box-shadow: 0 3px 8px rgba(0,0,0,.55);
  }
  .card-front { left: 314px; top: 113px; background: var(--card-front); }
  .card-back {
    left: 311px; top: 472px;
    background: linear-gradient(180deg, var(--card-back-top), var(--card-back-bottom));
  }

  .brand {
    position: absolute;
    display: flex;
    align-items: center;
    font-family: "Alegreya Sans", "Trebuchet MS", sans-serif;
    font-weight: 500;
  }
  .brand-mark { display: block; }
  .card-front .brand { left: 44px; top: 50px; color: var(--brand-grey); font-size: 44px; gap: 16px; }
  .card-front .brand-mark { width: 54px; height: 54px; background: var(--brand-grey); }
  .card-back .brand { left: 124px; top: 131px; color: var(--white); font-size: 58px; gap: 20px; }
  .card-back .brand-mark { width: 74px; height: 74px; background: var(--white); }

  .address, .contact-list {
    position: absolute;
    left: 43px;
    font-family: Roboto, Arial, sans-serif;
    font-size: 14px;
    color: var(--text-grey);
    margin: 0;
  }
  .address { top: 157px; line-height: 19px; font-style: normal; }
  .contact-list { top: 204px; list-style: none; padding: 0; line-height: 19px; }
  .contact-list li { display: flex; align-items: center; gap: 8px; }
  .contact-list svg { width: 13px; height: 13px; fill: var(--leaf-green); flex: none; }

  .staff-photo {
    position: absolute;
    left: 420px; top: 102px;
    width: 109px; height: 146px;
    border: 1px solid var(--photo-frame);
    border-radius: 10px;
    background: linear-gradient(180deg, var(--photo-fill), #c5c6c8);
  }
  .staff-name, .staff-role {
    position: absolute;
    left: 398px; width: 160px;
    text-align: center;
    font-family: "Roboto Condensed", "Arial Narrow", sans-serif;
    margin: 0;
  }
  .staff-name { top: 257px; font-size: 21px; font-weight: 700; color: var(--leaf-green); }
  .staff-role { top: 283px; font-size: 15px; color: var(--text-grey); }

  .back-url {
    position: absolute;
    left: 0; right: 0; top: 287px;
    text-align: center;
    font-family: Roboto, Arial, sans-serif;
    font-size: 14px;
    letter-spacing: 5.2px;
    color: var(--white);
  }
</style>
</head>
<body>
<div class="canvas">

  <section class="card card-front">
    <div class="brand"><span class="brand-mark"></span>Fernhale</div>

    <address class="address">4126 Linden Court<br>Juneau, Alaska 99801</address>

    <ul class="contact-list">
      <li><svg viewBox="0 0 16 16"><path d="M3 1l3 3-2 2c1 2 3 4 5 5l2-2 3 3-2 3C6 15 1 10 1 3z"/></svg>555 214 3860</li>
      <li><svg viewBox="0 0 16 16"><path d="M4 0h8v16H4zM5.5 2v10h5V2zM7 13.2h2v1.4H7z" fill-rule="evenodd"/></svg>555 782 1047</li>
      <li><svg viewBox="0 0 16 16"><path d="M4 1h8v4H4zM1 6h14v6h-3v3H4v-3H1zM5 10v3h6v-3z" fill-rule="evenodd"/></svg>555 390 6625</li>
      <li><svg viewBox="0 0 16 16"><path d="M1 3h14v10H1zM2 4.5v.5l6 4 6-4v-.5z" fill-rule="evenodd"/></svg>name@fernhale.com</li>
      <li><svg viewBox="0 0 16 16"><circle cx="8" cy="8" r="7"/></svg>www.fernhale.com</li>
    </ul>

    <div class="staff-photo" role="img" aria-label="Portrait photo of the sales person"></div>
    <p class="staff-name">DANIEL HART</p>
    <p class="staff-role">CEO/FOUNDER</p>
  </section>

  <section class="card card-back">
    <div class="brand"><span class="brand-mark"></span>Fernhale</div>
    <div class="back-url">www.fernhale.com</div>
  </section>

</div>
</body>
</html>
```